BUSINESS CARD DESIGN

NAME- DALE VORSKIN
PHONE NUMER - 555- 714-9082
EMAIL- OFFICE@TRV-GROUNDMAKRZ.COM
BACK OF CARD- SPEACIALIZES IN LAND CLEARING, FORESTRY MUCLHING AND EXCAVATION

Contact Information for Business Card

NAME- DALE VORSKIN PHONE NUMER - 555- 714-9082 EMAIL- OFFICE@TRV-GROUNDMAKRZ.COM BACK OF CARD- SPEACIALIZES IN LAND CLEARING , MUCLHING AND EXCAVATION

```html
<!DOCTYPE html>
<html lang="en">
<head>
<meta charset="utf-8">
<title>Dale Vorskin – Business Card</title>
<link href="https://fonts.googleapis.com/css2?family=Montserrat:wght@300;600;700&display=swap" rel="stylesheet">
<style>
  :root {
    --backdrop: #1b1b1b;
    --card: #f4f4f4;
    --ink: #262626;
    --icon: #2b2b2b;
    --icon-glyph: #f4f4f4;
  }
  * { margin: 0; padding: 0; box-sizing: border-box; }
  html, body {
    width: 1200px;
    height: 1059px;
    overflow: hidden;
    background: var(--backdrop);
  }
  .stage {
    position: relative;
    width: 1200px;
    height: 1059px;
  }
  .card {
    position: absolute;
    left: 255px;
    width: 690px;
    height: 392px;
    background: var(--card);
    border-radius: 18px;
    color: var(--ink);
    font-family: "Montserrat", sans-serif;
    text-align: center;
  }
  .card--front { top: 89px; }
  .card--back {
    top: 546px;
    display: flex;
    align-items: center;
    justify-content: center;
  }
  .holder-name {
    position: absolute;
    left: 0; right: 0;
    top: 66px;
    font-size: 44px;
    font-weight: 700;
    letter-spacing: 1px;
    line-height: 1;
  }
  .holder-role {
    position: absolute;
    left: 0; right: 0;
    top: 118px;
    font-size: 23px;
    font-weight: 300;
    letter-spacing: 1.5px;
    line-height: 1;
  }
  .contact-icons {
    position: absolute;
    left: 0; right: 0;
    top: 163px;
    display: flex;
    justify-content: center;
    gap: 3px;
  }
  .contact-icons svg { width: 24px; height: 24px; }
  .contact-line {
    position: absolute;
    left: 0; right: 0;
    font-size: 23px;
    font-weight: 300;
    letter-spacing: 1.2px;
    line-height: 1;
  }
  .contact-line--phone { top: 213px; }
  .contact-line--email { top: 254px; }
  .contact-line--web { top: 295px; }
  .specialties {
    font-size: 28px;
    font-weight: 600;
    letter-spacing: 1px;
    line-height: 46px;
    margin-top: 20px;
  }
</style>
</head>
<body>
<main class="stage">
  <section class="card card--front">
    <h1 class="holder-name">DALE VORSKIN</h1>
    <p class="holder-role">DIRECTOR</p>
    <div class="contact-icons">
      <svg viewBox="0 0 24 24" aria-label="Phone">
        <circle cx="12" cy="12" r="12" fill="var(--icon)"/>
        <path d="M6.5 9.5 Q12 6 17.5 9.5 L16.5 11 L14.5 10.5 L14.5 9.5 Q12 8.8 9.5 9.5 L9.5 10.5 L7.5 11 Z" fill="var(--icon-glyph)"/>
        <rect x="8" y="11.5" width="8" height="5.5" rx="1" fill="var(--icon-glyph)"/>
      </svg>
      <svg viewBox="0 0 24 24" aria-label="Email">
        <circle cx="12" cy="12" r="12" fill="var(--icon)"/>
        <rect x="6" y="8" width="12" height="8.5" fill="var(--icon-glyph)"/>
        <path d="M6 8 L12 13 L18 8" fill="none" stroke="var(--icon)" stroke-width="1"/>
      </svg>
      <svg viewBox="0 0 24 24" aria-label="Website">
        <circle cx="12" cy="12" r="12" fill="var(--icon)"/>
        <circle cx="12" cy="12" r="6" fill="var(--icon-glyph)"/>
        <ellipse cx="12" cy="12" rx="2.6" ry="6" fill="none" stroke="var(--icon)" stroke-width="0.9"/>
        <line x1="6" y1="12" x2="18" y2="12" stroke="var(--icon)" stroke-width="0.9"/>
      </svg>
    </div>
    <p class="contact-line contact-line--phone">555- 714-9082</p>
    <p class="contact-line contact-line--email">OFFICE@TRV-GROUNDMAKRZ.COM</p>
    <p class="contact-line contact-line--web">WWW.TRV-GROUNDMAKRZ.COM</p>
  </section>

  <section class="card card--back">
    <p class="specialties">SPEACIALIZES IN LAND CLEARING<br>MUCLHING AND EXCAVATION</p>
  </section>
</main>
</body>
</html>
```